Homeowners Insurance Provider Website

We are selling homeowners insurance policy / tenants Policy/Flood Insurance in USA in few states and planning expand nationally.

Our target audience are two folds: Customers (Buy policies) and Insurance Agents who wants to work with us to sell our policies to customers. But website should focus 80% on customers and 20% on agents. So, more customer focused user experience. Please note that there is no direct buy option for customers. They always go through insurance agents.

Customer focused, educational that makes buyer journey easy. We don’t want to come off as trying sell something as there is no direct sales involved from website.

Target Market(s)

Homeowners in USA and Insurance agent who sells these insurance.

Industry/Entity Type

Insurance

Number of Pages Required

4 page

Font styles to use
Other font styles liked:
• Open to suggestions

Colors

Designer to choose colors to be used in the design.

Requirements
Must have
• Three most important things: Trustworthy, Authentic, Simple
• Please use colors form logo and grays
• We like: www.hollowmere.com
• https://www.quillfenbrook.com/
• We need Agent Look up tool on home page similar to what is shown on example sites.
• Design:
• Home Page - Open to Ideas
• Insurance (Products) Landing Page - Info similar to: https://www.quillfenbrook.com/insurance/
• Agents Page - https://www.quillfenbrook.com/agents/
• Claims Page - Information similar to: https://www.quillfenbrook.com/claims-center/
• Site Navigation:
• Home
• Insurance
• Claims
• Agents
• About Us
• Contact Us
Nice to have
• Elegant, minimal and clean design that reflects trust and authenticity.
Should not have
• Slider or rotating images - prefer flat design. Not over powering design.

```html
<!DOCTYPE html>
<html lang="en">
<head>
<meta charset="utf-8">
<title>Hearthline Insurance Co. | Home</title>
<link rel="stylesheet" href="https://fonts.googleapis.com/css2?family=Montserrat:wght@500;600;700&family=Open+Sans:wght@400;600;700&display=swap">
<style>
:root{
  --navy:#1f3a7a;
  --navy-deep:#182f66;
  --navy-band:rgba(47,74,140,.88);
  --red:#d3202b;
  --ink:#333;
  --muted:#666;
  --line:#d9d9d9;
  --panel:#f2f2f2;
  --white:#fff;
}
*{box-sizing:border-box;margin:0;padding:0}
html,body{width:717px;height:1200px;overflow:hidden;background:var(--white)}
body{font-family:"Open Sans",Arial,sans-serif;color:var(--ink)}
.page{position:relative;width:717px;height:1200px;overflow:hidden}
.abs{position:absolute}
.heading{font-family:"Montserrat",Arial,sans-serif}

/* header */
.site-header{position:absolute;left:0;top:0;width:717px;height:56px;background:var(--white)}
.brand{position:absolute;left:80px;top:9px;display:flex;align-items:center;gap:8px}
.brand-mark{width:28px;height:28px;background:var(--navy);border-radius:3px}
.brand-name{font-family:"Montserrat",Arial,sans-serif;font-weight:600;color:var(--navy);line-height:1}
.brand-name .l1{display:block;font-size:17px;letter-spacing:.2px}
.brand-name .l2{display:block;font-size:9.6px;letter-spacing:2.6px;margin-top:2px}
.call{position:absolute;left:462px;top:10px;display:flex;align-items:center;gap:6px}
.call-icon{width:16px;height:16px;border-radius:50%;background:var(--navy);display:flex;align-items:center;justify-content:center}
.call-label{font-family:"Montserrat",Arial,sans-serif;font-size:5.6px;font-weight:700;color:var(--navy);line-height:1}
.call-number{font-family:"Montserrat",Arial,sans-serif;font-size:10.5px;font-weight:600;color:var(--red);line-height:1.1}
.search{position:absolute;left:570px;top:11px;width:67px;height:16px;border:1px solid var(--line);background:#fafafa;font-size:5px;color:#555;padding:0 6px;display:flex;align-items:center;justify-content:space-between}
.main-nav{position:absolute;top:37px;left:338px;display:flex;gap:0;font-family:"Montserrat",Arial,sans-serif;font-size:6.8px;font-weight:600;color:#222}
.main-nav a{display:block;padding:3px 4px;color:inherit;text-decoration:none}
.main-nav a.active{background:var(--red);color:var(--white)}
.main-nav a+a{margin-left:10px}

/* hero */
.hero{position:absolute;left:0;top:56px;width:717px;height:329px}
.hero-photo{position:absolute;inset:0;background:linear-gradient(100deg,#3e5530 0%,#6f7a6a 28%,#9aa2a6 50%,#8b9294 70%,#5e6b4f 100%)}
.hero-copy{position:absolute;left:434px;top:87px;width:210px;color:var(--white)}
.hero-title{font-family:"Montserrat",Arial,sans-serif;font-weight:700;font-size:20px;line-height:22px;letter-spacing:.3px}
.hero-text{font-size:10px;font-weight:600;line-height:11.5px;margin-top:7px}
.btn-primary{display:inline-block;margin-top:20px;background:var(--red);color:var(--white);font-family:"Montserrat",Arial,sans-serif;font-weight:700;font-size:10.5px;padding:7px 11px;letter-spacing:.3px}

/* section titles */
.section-title{text-align:center;font-family:"Montserrat",Arial,sans-serif;color:var(--navy);font-size:12.5px;font-weight:500;letter-spacing:.3px}
.section-title strong{font-weight:700}
.title-rule{width:26px;height:2px;background:var(--red);margin:0 auto}

/* products */
.products{position:absolute;left:0;top:385px;width:717px;height:283px;background:var(--white)}
.product{position:absolute;top:82px;width:130px;text-align:center}
.product-icon{width:73px;height:73px;border-radius:50%;background:var(--navy);margin:0 auto;display:flex;align-items:center;justify-content:center}
.product-name{margin-top:28px;font-family:"Montserrat",Arial,sans-serif;font-weight:700;font-size:8.5px;color:var(--navy);letter-spacing:.3px}
.product-text{margin-top:8px;font-size:6.6px;line-height:9.6px;color:#333}

/* welcome */
.welcome{position:absolute;left:0;top:668px;width:717px;height:335px;background:var(--panel)}
.welcome-kicker{font-family:"Montserrat",Arial,sans-serif;color:var(--navy);font-size:10px;font-weight:500;text-align:center}
.welcome-title{font-family:"Montserrat",Arial,sans-serif;color:var(--navy);font-size:13px;font-weight:700;text-align:center;margin-top:1px}
.welcome-text{width:275px;margin:0 auto;text-align:center;font-size:6.6px;line-height:9.6px;color:#333}
.feature{position:absolute;top:137px;width:253px;height:161px}
.feature-photo{position:absolute;inset:0}
.feature-band{position:absolute;left:0;bottom:0;width:100%;height:29px;background:var(--navy-band);display:flex;align-items:center;justify-content:space-between;padding:0 12px 0 11px;color:var(--white);font-family:"Montserrat",Arial,sans-serif;font-weight:700;font-size:10.5px;letter-spacing:.3px}

/* footer */
.site-footer{position:absolute;left:0;top:1003px;width:717px;height:197px;background:var(--white)}
.footer-brand{position:absolute;left:80px;top:30px}
.follow{position:absolute;left:81px;top:93px;display:flex;align-items:center;gap:6px;font-family:"Montserrat",Arial,sans-serif;font-size:6.4px;font-weight:700;color:var(--navy)}
.follow .dot{width:16px;height:16px;border-radius:50%;background:var(--navy)}
.follow .dot.sky{background:#1da1f2}
.follow .dot.deep{background:#1b2c5c}
.follow span:first-child{margin-right:2px}
.footer-col{position:absolute;top:33px}
.footer-head{font-family:"Montserrat",Arial,sans-serif;font-size:6.4px;font-weight:700;color:var(--navy);letter-spacing:.3px}
.contact-row{display:flex;gap:8px;font-size:6.6px;line-height:9.5px;color:#333;margin-top:10px}
.contact-row svg{flex:none;margin-top:1px}
.footer-menu{list-style:none;margin-top:9px;font-size:6.6px;line-height:9.6px;color:#333}
.newsletter-input{margin-top:10px;width:125px;height:25px;border:1px solid #999;font-size:6.4px;color:#444;padding:0 10px;display:flex;align-items:center}
.btn-signup{margin-top:10px;width:45px;height:18px;background:var(--red);color:var(--white);font-family:"Montserrat",Arial,sans-serif;font-weight:700;font-size:6.4px;display:flex;align-items:center;justify-content:center}
.footer-rule{position:absolute;left:80px;top:145px;width:557px;height:1px;background:var(--line)}
.copyright{position:absolute;left:0;top:166px;width:717px;text-align:center;font-size:6.6px;color:#666}
</style>
</head>
<body>
<div class="page">

  <header class="site-header">
    <div class="brand">
      <div class="brand-mark"></div>
      <div class="brand-name"><span class="l1">HEARTHLINE</span><span class="l2">INSURANCE CO.</span></div>
    </div>
    <div class="call">
      <div class="call-icon">
        <svg width="8" height="8" viewBox="0 0 24 24"><path fill="#fff" d="M6.6 10.8a15.2 15.2 0 0 0 6.6 6.6l2.2-2.2c.3-.3.7-.4 1-.2 1.1.4 2.3.6 3.6.6.6 0 1 .4 1 1V20c0 .6-.4 1-1 1A17 17 0 0 1 3 4c0-.6.4-1 1-1h3.5c.6 0 1 .4 1 1 0 1.3.2 2.5.6 3.6.1.3 0 .7-.2 1z"/></svg>
      </div>
      <div>
        <div class="call-label">CALL US :</div>
        <div class="call-number">800.555.0142</div>
      </div>
    </div>
    <div class="search"><span>SEARCH</span>
      <svg width="6" height="6" viewBox="0 0 24 24"><circle cx="10" cy="10" r="7" fill="none" stroke="#333" stroke-width="3"/><path d="M15 15l6 6" stroke="#333" stroke-width="3"/></svg>
    </div>
    <nav class="main-nav">
      <a class="active">HOME</a><a>INSURANCE</a><a>CLAIMS</a><a>AGENTS</a><a>ABOUT US</a><a>CONTACT US</a>
    </nav>
  </header>

  <section class="hero">
    <div class="hero-photo" role="img" aria-label="Photo of a smiling couple standing in front of their white two-storey house with trees"></div>
    <div class="hero-copy">
      <h1 class="hero-title">HOMEOWNERS<br>INSURANCE</h1>
      <p class="hero-text">It is a long established fact that a reader will be distracted by the readable content of a page when looking.</p>
      <span class="btn-primary">READ MORE</span>
    </div>
  </section>

  <section class="products">
    <h2 class="section-title abs" style="left:0;width:717px;top:28px">OUR <strong>PRODUCTS</strong></h2>
    <div class="title-rule abs" style="left:345px;top:49px"></div>

    <div class="product" style="left:73px">
      <div class="product-icon">
        <svg width="30" height="28" viewBox="0 0 30 28"><path fill="#fff" d="M15 2 1 14h4v12h8v-8h4v8h8V14h4z"/></svg>
      </div>
      <div class="product-name">HOMEOWNERS</div>
      <p class="product-text">There are many variations of passages of Lorem Ipsum available, but the majority have suffered alteration in some form, by injected humou.</p>
    </div>
    <div class="product" style="left:212px">
      <div class="product-icon">
        <svg width="24" height="34" viewBox="0 0 24 34"><rect x="3" y="1" width="18" height="30" fill="#fff"/><rect x="0" y="31" width="24" height="2" fill="#fff"/><g fill="#1f3a7a"><rect x="6" y="4" width="3" height="3"/><rect x="10.5" y="4" width="3" height="3"/><rect x="15" y="4" width="3" height="3"/><rect x="6" y="9" width="3" height="3"/><rect x="10.5" y="9" width="3" height="3"/><rect x="15" y="9" width="3" height="3"/><rect x="6" y="14" width="3" height="3"/><rect x="10.5" y="14" width="3" height="3"/><rect x="15" y="14" width="3" height="3"/><rect x="6" y="19" width="3" height="3"/><rect x="10.5" y="19" width="3" height="3"/><rect x="15" y="19" width="3" height="3"/><rect x="9.5" y="25" width="5" height="6"/></g></svg>
      </div>
      <div class="product-name">RENTERS/CONDO</div>
      <p class="product-text">There are many variations of passages of Lorem Ipsum available, but the majority have suffered alteration in some form, by injected humou.</p>
    </div>
    <div class="product" style="left:363px">
      <div class="product-icon">
        <svg width="38" height="32" viewBox="0 0 38 32"><path fill="#fff" d="M22 2 6 15h4v15h24V15h4z"/><rect x="28" y="4" width="4" height="7" fill="#fff"/><path fill="#1f3a7a" d="M16 30c-4 0-6-3-5-6 1-2 3-3 3-6 3 2 4 4 4 6 1-1 1-2 1-3 2 2 3 4 2 6-1 2-3 3-5 3z"/></svg>
      </div>
      <div class="product-name">DWELLING FIRE</div>
      <p class="product-text">There are many variations of passages of Lorem Ipsum available, but the majority have suffered alteration in some form, by injected humou.</p>
    </div>
    <div class="product" style="left:515px">
      <div class="product-icon">
        <svg width="28" height="34" viewBox="0 0 28 34"><path fill="none" stroke="#fff" stroke-width="2.4" d="M14 2a9 9 0 0 0-9 9c0 7 9 15 9 15s9-8 9-15a9 9 0 0 0-9-9z"/><circle cx="14" cy="11" r="3.2" fill="none" stroke="#fff" stroke-width="2.2"/><ellipse cx="14" cy="29" rx="11" ry="3" fill="none" stroke="#fff" stroke-width="2"/></svg>
      </div>
      <div class="product-name">AGENT LOCATOR TOOL</div>
      <p class="product-text">There are many variations of passages of Lorem Ipsum available, but the majority have suffered alteration in some form, by injected humou.</p>
    </div>
  </section>

  <section class="welcome">
    <div class="abs" style="left:0;width:717px;top:30px">
      <div class="welcome-kicker">WELCOME TO</div>
      <h2 class="welcome-title">HEARTHLINE INSURANCE &amp; CO</h2>
    </div>
    <div class="title-rule abs" style="left:345px;top:64px"></div>
    <p class="welcome-text abs" style="left:221px;top:83px;margin:0">It is a long established fact that a reader will be distracted by the readable content of a page when looking at its layout. The point of using Lorem Ipsum is that it has a more-or-less normal distribution of letters, as opposed to</p>

    <a class="feature" style="left:97px">
      <div class="feature-photo" role="img" aria-label="Photo of people reviewing policy papers and a tablet at a white desk" style="background:linear-gradient(135deg,#e9ecef 0%,#c9cfd6 45%,#8ea0bd 70%,#dcdfe3 100%)"></div>
      <div class="feature-band"><span>TENANTS POLICY</span>
        <svg width="8" height="12" viewBox="0 0 8 12"><path d="M1 1l5 5-5 5" fill="none" stroke="#fff" stroke-width="1.8"/></svg></div>
    </a>
    <a class="feature" style="left:365px">
      <div class="feature-photo" role="img" aria-label="Photo of a red wooden house tilted and partly submerged in flood water" style="background:linear-gradient(180deg,#5f7a4a 0%,#8a8f7f 40%,#9a5040 55%,#7c8a90 75%,#6f7f86 100%)"></div>
      <div class="feature-band"><span>FLOOD INSURANCE</span>
        <svg width="8" height="12" viewBox="0 0 8 12"><path d="M1 1l5 5-5 5" fill="none" stroke="#fff" stroke-width="1.8"/></svg></div>
    </a>
  </section>

  <footer class="site-footer">
    <div class="footer-brand brand" style="left:80px;top:30px">
      <div class="brand-mark"></div>
      <div class="brand-name"><span class="l1">HEARTHLINE</span><span class="l2">INSURANCE CO.</span></div>
    </div>
    <div class="follow"><span>FOLLOW US</span><span class="dot"></span><span class="dot sky"></span><span class="dot deep"></span></div>

    <div class="footer-col" style="left:286px">
      <div class="footer-head">CONTACT US</div>
      <div class="contact-row">
        <svg width="6" height="8" viewBox="0 0 12 16"><path fill="#1f3a7a" d="M6 0a6 6 0 0 0-6 6c0 4.5 6 10 6 10s6-5.5 6-10a6 6 0 0 0-6-6zm0 8.2A2.2 2.2 0 1 1 6 3.8a2.2 2.2 0 0 1 0 4.4z"/></svg>
        <span>218 Willow Bend Lane<br>Franklin, TN 37064</span>
      </div>
      <div class="contact-row" style="margin-top:8px">
        <svg width="7" height="7" viewBox="0 0 24 24"><path fill="#1f3a7a" d="M6.6 10.8a15.2 15.2 0 0 0 6.6 6.6l2.2-2.2c.3-.3.7-.4 1-.2 1.1.4 2.3.6 3.6.6.6 0 1 .4 1 1V20c0 .6-.4 1-1 1A17 17 0 0 1 3 4c0-.6.4-1 1-1h3.5c.6 0 1 .4 1 1 0 1.3.2 2.5.6 3.6.1.3 0 .7-.2 1z"/></svg>
        <span>800.555.0142</span>
      </div>
      <div class="contact-row" style="margin-top:12px">
        <svg width="8" height="6" viewBox="0 0 16 12"><rect width="16" height="12" fill="#1f3a7a"/><path d="M0 0l8 6 8-6" fill="none" stroke="#fff" stroke-width="1.4"/></svg>
        <span>info@hearthline.com</span>
      </div>
    </div>

    <div class="footer-col" style="left:418px">
      <div class="footer-head">MENU</div>
      <ul class="footer-menu">
        <li>Home</li><li>Insurance</li><li>Claims</li><li>Agents</li><li>About us</li><li>Contact us.</li>
      </ul>
    </div>

    <div class="footer-col" style="left:513px">
      <div class="footer-head">NEWSLETTER</div>
      <div class="newsletter-input">E mail id</div>
      <div class="btn-signup">SIGNUP</div>
    </div>

    <div class="footer-rule"></div>
    <p class="copyright">Copyrights @ 2018 All Rights Reserved</p>
  </footer>

</div>
</body>
</html>
```